Business Card Design Project

- makeup artist business card

- original and creative

- Elegant design

- Feel free to come out with cool designs but stick to being elegant and attractive

- Design relates to makeup

- includes name, occupation, contact numbers, email, website

- regular size business card

- round corner card

- double sided

- on 1 side it should just have the website name in the center " moonveilstudio.net "

Industry/Entity Type

Business

Requirements
Must have
• Delia Marsh
Makeup Artist
USA: +1 (415)772-0461
Singapore: +65 82307915
deliamarsh@moonveilstudio.net
www.moonveilstudio.net
Should not have
• nothing cartoon looking.
Pictures of makeup being grab from the internet.. Examples: eyes or lips.

```html
<!DOCTYPE html>
<html lang="en">
<head>
<meta charset="utf-8">
<title>Delia Marsh – Makeup Artist Business Card</title>
<link rel="stylesheet" href="https://fonts.googleapis.com/css2?family=Arimo:wght@400;700&family=Gelasio:ital,wght@0,700;1,400&display=swap">
<style>
  :root {
    --backdrop: #2b2b2d;
    --card: #ffffff;
    --plum: #8c1d6c;
    --plum-soft: #a2357f;
    --rose: #d6408b;
    --rose-light: #e88cb9;
    --ink: #333333;
    --ink-soft: #555555;
  }
  * { margin: 0; padding: 0; box-sizing: border-box; }
  html, body {
    width: 1200px; height: 944px; overflow: hidden;
    background: var(--backdrop);
    font-family: "Arimo", Arial, sans-serif;
  }
  .canvas { position: relative; width: 1200px; height: 944px; }

  .card {
    position: absolute;
    width: 600px; height: 345px;
    background: var(--card);
    border-radius: 24px;
    overflow: hidden;
    box-shadow: 0 10px 26px rgba(0,0,0,0.45);
  }
  .card--front { left: 60px; top: 100px; }
  .card--back { left: 540px; top: 500px; }

  /* Front side */
  .front-web {
    position: absolute; left: 0; right: 0; top: 150px;
    text-align: center;
    font-size: 30px; letter-spacing: 0.5px;
    color: var(--rose);
  }
  .front-web .dots { letter-spacing: 6px; font-size: 22px; vertical-align: 4px; }
  .front-web .tld { color: var(--ink); }

  /* Back side */
  .waves { position: absolute; inset: 0; width: 600px; height: 345px; }
  .brand {
    position: absolute; left: 34px; top: 36px;
    display: flex; align-items: center; gap: 10px;
    font-size: 30px; line-height: 34px;
    color: var(--plum-soft);
  }
  .brand .mark {
    width: 14px; height: 14px; border-radius: 50%;
    background: var(--plum-soft); flex: none;
  }

  .identity {
    position: absolute; right: 40px; top: 78px;
    text-align: left;
  }
  .identity .name {
    font-family: "Gelasio", Georgia, serif; font-weight: 700;
    font-size: 22px; color: #222;
  }
  .identity .role {
    font-family: "Gelasio", Georgia, serif; font-style: italic;
    font-size: 15px; color: var(--rose);
  }

  .contacts {
    position: absolute; left: 300px; top: 168px;
    list-style: none;
    font-size: 14px; color: var(--ink-soft);
  }
  .contacts li { display: flex; align-items: center; height: 21px; }
  .contacts svg { width: 12px; height: 12px; margin-right: 7px; flex: none; }

  .back-web {
    position: absolute; left: 0; right: 0; bottom: 14px;
    text-align: center;
    font-size: 21px; letter-spacing: 3px;
    color: #fff;
  }
  .back-web .dots { letter-spacing: 5px; font-size: 16px; vertical-align: 3px; }
</style>
</head>
<body>
<main class="canvas">

  <section class="card card--front" aria-label="Business card front">
    <p class="front-web"><span class="dots">••••</span> moonveilstudio<span class="tld">.net</span> <span class="dots">••</span></p>
  </section>

  <section class="card card--back" aria-label="Business card back">
    <svg class="waves" viewBox="0 0 600 345" aria-hidden="true">
      <path d="M0 205 C200 212 400 248 600 270 L600 345 L0 345 Z" fill="var(--rose-light)"/>
      <path d="M0 218 C200 228 400 266 600 290 L600 345 L0 345 Z" fill="var(--plum)"/>
      <path d="M0 296 C200 282 420 290 600 306 L600 345 L0 345 Z" fill="var(--plum-soft)"/>
      <path d="M0 296 C200 282 420 290 600 306" fill="none" stroke="var(--rose-light)" stroke-width="3"/>
    </svg>

    <div class="brand"><span class="mark" aria-hidden="true"></span><span class="brand-name">moonveil studio</span></div>

    <div class="identity">
      <p class="name">Delia Marsh</p>
      <p class="role">Makeup Artist</p>
    </div>

    <ul class="contacts">
      <li><svg viewBox="0 0 12 12"><circle cx="6" cy="6" r="5.5" fill="var(--rose)"/><path d="M4 3.5 L5.2 3.5 L5.6 5 L4.9 5.5 C5.2 6.4 5.6 6.8 6.5 7.1 L7 6.4 L8.5 6.8 L8.5 8 C6 8.2 3.8 6 4 3.5Z" fill="#fff"/></svg>USA: +1 (415)772-0461</li>
      <li><svg viewBox="0 0 12 12"><circle cx="6" cy="6" r="5.5" fill="var(--rose)"/><path d="M4 3.5 L5.2 3.5 L5.6 5 L4.9 5.5 C5.2 6.4 5.6 6.8 6.5 7.1 L7 6.4 L8.5 6.8 L8.5 8 C6 8.2 3.8 6 4 3.5Z" fill="#fff"/></svg>Singapore: +65 82307915</li>
      <li><svg viewBox="0 0 12 12"><rect x="0.5" y="2" width="11" height="8" rx="1.5" fill="var(--rose)"/><path d="M1.5 3 L6 6.5 L10.5 3" fill="none" stroke="#fff" stroke-width="1"/></svg>deliamarsh@moonveilstudio.net</li>
    </ul>

    <p class="back-web"><span class="dots">••••</span> moonveilstudio.net</p>
  </section>

</main>
</body>
</html>
```